Consulting company requires a logo and business card design

I require a logo/business card design for a new company based in Sexsmith Alberta called TallMarsh Integrity Consulting Ltd. I plan to provide the following services: Construction management/inspection for the oil and gas industry, as well as general consulting for Asset Management, fleet management, etc. Have attached a copy of resume for use as guide for

Target Market(s)

Businesses within the oil and gas production, construction and shipping industry

Industry/Entity Type

Oil And Gas

Contact Information for Business Card

Believe should highlight, services offered, safety, quality,

Logo Text

TallMarsh Integrity Consulting (TMIC) ?

Font styles to use
Script

Requirements
Must have
• Open to all options

```html
<!DOCTYPE html>
<html lang="en">
<head>
<meta charset="utf-8">
<title>TallMarsh Integrity Consulting Ltd – Business Card</title>
<link rel="stylesheet" href="https://fonts.googleapis.com/css2?family=Lato:wght@700&family=Source+Sans+3:wght@400;600&display=swap">
<style>
  :root {
    --stage: #000000;
    --card: #323335;
    --accent: #f7bb0e;
    --ink: #ffffff;
    --divider: #3d3e41;
  }
  * { margin: 0; padding: 0; box-sizing: border-box; }
  html, body {
    width: 1200px; height: 900px; overflow: hidden;
    background: var(--stage);
    font-family: "Source Sans 3", "Myriad Pro", sans-serif;
    color: var(--ink);
  }
  .stage { position: relative; width: 1200px; height: 900px; }
  .card {
    position: absolute; top: 271px;
    width: 457px; height: 281px;
    background: var(--card);
    border-radius: 14px;
  }
  .card--front { left: 137px; }
  .card--back { left: 626px; }

  .front-mark {
    position: absolute; left: 62px; top: 108px;
    font-family: "Lato", sans-serif; font-weight: 700;
    font-size: 40px; color: var(--accent); letter-spacing: 1px;
  }
  .front-divider {
    position: absolute; left: 201px; top: 82px;
    width: 1px; height: 130px; background: var(--divider);
  }
  .contact { position: absolute; left: 246px; top: 72px; }
  .contact__name { font-size: 19px; color: var(--accent); line-height: 22px; }
  .contact__role { font-size: 13px; line-height: 16px; }
  .contact__address { margin-top: 12px; font-size: 13px; line-height: 16px; }
  .contact__list { margin-top: 11px; list-style: none; font-size: 13px; line-height: 17px; }
  .contact__list li { display: flex; align-items: center; }
  .contact__list svg { width: 10px; height: 10px; margin: 0 6px 0 0; fill: var(--accent); flex: none; }

  .brand {
    position: absolute; left: 0; right: 0; top: 54px;
    display: flex; align-items: center; justify-content: center; gap: 12px;
  }
  .brand__dot {
    width: 26px; height: 26px; border-radius: 50%;
    border: 3px solid var(--accent); flex: none;
  }
  .brand__name {
    font-family: "Lato", sans-serif; font-weight: 700;
    font-size: 22px; line-height: 27px; color: var(--accent);
  }
  .tagline {
    position: absolute; left: 0; right: 0; top: 171px;
    text-align: center; font-weight: 600;
    font-size: 14.5px; line-height: 19px;
  }
</style>
</head>
<body>
<main class="stage">
  <section class="card card--front">
    <div class="front-mark">TMIC</div>
    <div class="front-divider"></div>
    <div class="contact">
      <p class="contact__name">Marcus Hale</p>
      <p class="contact__role">Managing Director</p>
      <p class="contact__address">12345, Address Goes Here<br>Country Name, 123456.</p>
      <ul class="contact__list">
        <li><svg viewBox="0 0 10 10"><path d="M2 0.5 L3.6 2.6 L2.8 3.6 Q4 6 6.4 7.2 L7.4 6.4 L9.5 8 L8.4 9.5 Q3.5 9 0.5 1.6 Z"/></svg>044-987 654 321</li>
        <li><svg viewBox="0 0 10 10"><path d="M0.5 2 H9.5 V8 H0.5 Z M0.5 2 L5 5.3 L9.5 2" fill="var(--accent)" stroke="var(--card)" stroke-width="0.8"/></svg>info@tallmarsh.example</li>
        <li><svg viewBox="0 0 10 10"><path d="M4 6 L6 4 M3.5 4.5 L1.6 6.4 A1.4 1.4 0 0 0 3.6 8.4 L5.5 6.5 M6.5 5.5 L8.4 3.6 A1.4 1.4 0 0 0 6.4 1.6 L4.5 3.5" fill="none" stroke="var(--accent)" stroke-width="1.3" stroke-linecap="round"/></svg>www.tallmarsh.example</li>
      </ul>
    </div>
  </section>

  <section class="card card--back">
    <div class="brand">
      <span class="brand__dot"></span>
      <p class="brand__name">TallMarsh Integrity<br>Consulting Ltd</p>
    </div>
    <p class="tagline">We are a construction management/inspection<br>for the oil and gas industry, as well as general<br>consulting for Asset Management, fleet management.</p>
  </section>
</main>
</body>
</html>
```